Heritage Hollow Business Cards

Require a business card design. <br/><br/>Needs to include logo (either round or long version) plus these details:<br/>Maya Torvell<br/>Heritage Hollow<br/>maya@kelvadtrading.com.au<br/>02 6481 7395<br/>PO Box Glenwarra NSW 2791<br/>www.heritagehollow.com.au<br/><br/>I need in an editable format so that I can create for multiple staff members. <br/><br/>

Target Market(s)

We are an online store selling renovation products to home owners are builders. Looking for a classic classy design.

Industry/Entity Type

Home And Garden

Contact Information for Business Card

Maya Torvell
Heritage Hollow
maya@kelvadtrading.com.au
02 6481 7395
PO Box Glenwarra NSW 2791
www.heritagehollow.com.au

Colors

Designer to choose colors to be used in the design.

Requirements
Must have
• Must include Logo.

```html
<!DOCTYPE html>
<html lang="en">
<head>
<meta charset="utf-8">
<title>Heritage Hollow Business Cards</title>
<link href="https://fonts.googleapis.com/css2?family=Roboto:wght@400;500;700&display=swap" rel="stylesheet">
<style>
  :root {
    --backdrop: #e9e7e4;
    --card-dark: #1d1b1b;
    --card-light: #ffffff;
    --ink: #2a2a2a;
    --ink-soft: #3a3a3a;
    --on-dark: #f2f2f2;
    --rule: #2a2a2a;
  }
  * { margin: 0; padding: 0; box-sizing: border-box; }
  html, body { width: 1200px; height: 716px; overflow: hidden; }
  body {
    background: var(--backdrop);
    font-family: "Roboto", sans-serif;
    position: relative;
  }
  .card {
    position: absolute;
    top: 205px;
    width: 500px;
    height: 306px;
    border-radius: 3px;
    box-shadow: 0 6px 18px rgba(0,0,0,0.18);
  }
  .card--front { left: 70px; background: var(--card-dark); }
  .card--back { left: 630px; background: var(--card-light); }

  .front-mark {
    position: absolute;
    left: 50%; top: 50%;
    width: 150px; height: 150px;
    transform: translate(-50%, -50%);
    border: 1px solid var(--on-dark);
    border-radius: 50%;
    display: flex; align-items: center; justify-content: center;
    text-align: center;
  }
  .front-mark__name {
    color: var(--on-dark);
    font-size: 22px;
    font-weight: 500;
    line-height: 1.15;
  }

  .back-brand {
    position: absolute;
    left: 26px; top: 142px;
    display: flex; align-items: center; gap: 8px;
  }
  .back-brand__dot {
    width: 14px; height: 14px;
    border: 1.5px solid var(--ink);
    border-radius: 50%;
  }
  .back-brand__name {
    color: var(--ink);
    font-size: 23px;
    font-weight: 500;
  }
  .divider {
    position: absolute;
    left: 262px; top: 100px;
    width: 1.5px; height: 130px;
    background: var(--rule);
  }
  .contact {
    position: absolute;
    left: 278px; top: 104px;
    color: var(--ink-soft);
    font-size: 12.5px;
    line-height: 1.35;
  }
  .contact__name { font-size: 16px; font-weight: 700; color: var(--ink); }
  .contact__company { margin-bottom: 6px; }
  .contact__address { margin-bottom: 2px; }
  .contact__line { display: flex; align-items: center; gap: 6px; }
  .contact__icon { width: 11px; height: 11px; fill: var(--ink); flex: none; }
</style>
</head>
<body>
  <section class="card card--front" aria-label="Card front">
    <div class="front-mark">
      <span class="front-mark__name">Heritage<br>Hollow</span>
    </div>
  </section>

  <section class="card card--back" aria-label="Card back">
    <div class="back-brand">
      <span class="back-brand__dot"></span>
      <span class="back-brand__name">Heritage Hollow</span>
    </div>
    <div class="divider"></div>
    <div class="contact">
      <div class="contact__name">Maya Torvell</div>
      <div class="contact__company">Heritage Hollow</div>
      <div class="contact__address">PO Box Glenwarra<br>NSW 2791</div>
      <div class="contact__line">
        <svg class="contact__icon" viewBox="0 0 24 24" aria-hidden="true"><path d="M6.6 10.8a15.1 15.1 0 0 0 6.6 6.6l2.2-2.2c.3-.3.7-.4 1-.2 1.1.4 2.3.6 3.6.6.6 0 1 .4 1 1V20c0 .6-.4 1-1 1C10.6 21 3 13.4 3 4c0-.6.4-1 1-1h3.5c.6 0 1 .4 1 1 0 1.3.2 2.5.6 3.6.1.3 0 .7-.2 1z"/></svg>
        <span>02 6481 7395</span>
      </div>
      <div class="contact__line">
        <svg class="contact__icon" viewBox="0 0 24 24" aria-hidden="true"><path d="M2 5h20v14H2z" fill="none" stroke="currentColor"/><path d="M2 5h20v14H2V5zm2 2v.5l8 5 8-5V7H4zm0 2.8V17h16V9.8l-8 5-8-5z"/></svg>
        <span>maya@kelvadtrading.com.au</span>
      </div>
      <div class="contact__line">
        <svg class="contact__icon" viewBox="0 0 24 24" aria-hidden="true"><path d="M12 2a10 10 0 1 0 0 20 10 10 0 0 0 0-20zm-1 17.9A8 8 0 0 1 4.1 10.9L9 16v1a2 2 0 0 0 2 2zm6.9-2.5A2 2 0 0 0 16 16h-1v-3a1 1 0 0 0-1-1H8v-2h2a1 1 0 0 0 1-1V7h2a2 2 0 0 0 2-2v-.4a8 8 0 0 1 2.9 12.8z"/></svg>
        <span>www.heritagehollow.com.au</span>
      </div>
    </div>
  </section>
</body>
</html>
```